Business Card Design Project

I require a business card with the following information on them for various different people;
name
m:
f:
e:
I have a logo already and will attached that. We are in the construction industry. I require something clean and simple but eye catching at the same time. You can use another colour with our logo if you like and you can style the logo as well if you wish. I am open.
Also it needs to be front and back design.
Industry/Entity Type
Construction
Requirements
Must have
- Logo, name, mobile, fax and email address.
Front and back design

```html
<!DOCTYPE html>
<html lang="en">
<head>
<meta charset="utf-8">
<title>Northfield Homes — Business Card</title>
<link rel="stylesheet" href="https://fonts.googleapis.com/css2?family=Source+Sans+3:wght@400;600;700&display=swap">
<style>
  :root {
    --backdrop: #a57f24;
    --card: #ffffff;
    --green: #5cb02c;
    --green-dark: #4fa323;
    --lime: #b5dc5c;
    --charcoal: #363636;
    --ink: #222222;
  }
  * { box-sizing: border-box; margin: 0; padding: 0; }
  html, body { width: 1200px; height: 686px; overflow: hidden; }
  body {
    background: var(--backdrop);
    font-family: "Source Sans 3", sans-serif;
    position: relative;
  }
  .card {
    position: absolute;
    width: 510px;
    height: 291px;
    background: var(--card);
    border-radius: 15px;
    overflow: hidden;
    box-shadow: 0 1px 3px rgba(0,0,0,0.45);
  }
  .card--front { left: 67px; top: 116px; }
  .card--back { left: 621px; top: 303px; }
  .card-bands { position: absolute; left: 0; bottom: 0; width: 510px; height: 30px; }

  .brand {
    position: absolute;
    left: 0; right: 0;
    display: flex;
    align-items: center;
    justify-content: center;
    gap: 10px;
    color: var(--green);
    font-weight: 400;
  }
  .card--front .brand { top: 84px; font-size: 40px; }
  .card--back .brand { top: 104px; font-size: 46px; }
  .brand-square { background: var(--green); flex: none; }
  .card--front .brand-square { width: 30px; height: 30px; }
  .card--back .brand-square { width: 36px; height: 36px; }

  .contact {
    position: absolute;
    top: 154px; left: 0; right: 0;
    text-align: center;
    color: var(--ink);
    font-size: 13px;
  }
  .contact-name {
    color: var(--green);
    font-weight: 700;
    font-size: 16px;
    margin-bottom: 4px;
  }
  .contact-row { display: flex; justify-content: center; gap: 16px; line-height: 18px; }
  .contact-item { display: inline-flex; align-items: center; gap: 2px; }
  .contact-icon { width: 12px; height: 10px; fill: var(--green); }
</style>
</head>
<body>

<section class="card card--front" aria-label="Business card front">
  <div class="brand"><span class="brand-square"></span><span class="brand-name">Northfield Homes</span></div>

  <div class="contact">
    <p class="contact-name">Your Name</p>
    <div class="contact-row">
      <span class="contact-item">
        <svg class="contact-icon" viewBox="0 0 12 10" aria-hidden="true"><path d="M1 6c2-3 8-3 10 0l-1 2-2-1V6C7 5 5 5 4 6v1L2 8z"/></svg>
        123-456-7890
      </span>
      <span class="contact-item">
        <svg class="contact-icon" viewBox="0 0 12 10" aria-hidden="true"><path d="M3 0h6v3H3zM1 4h10v5H1zM3 6h6v1H3z"/></svg>
        123-456-7890
      </span>
    </div>
    <div class="contact-row">
      <span class="contact-item">
        <svg class="contact-icon" viewBox="0 0 12 10" aria-hidden="true"><path d="M1 2h10v7H1zM1 2l5 4 5-4" stroke="#fff" stroke-width="0.8"/></svg>
        name@website.com
      </span>
    </div>
  </div>

  <svg class="card-bands" viewBox="0 0 510 30" aria-hidden="true">
    <defs>
      <linearGradient id="band-front" x1="0" x2="1" y1="0" y2="0">
        <stop offset="0" stop-color="var(--lime)"/>
        <stop offset="1" stop-color="var(--green-dark)"/>
      </linearGradient>
    </defs>
    <polygon points="0,14 284,14 277,30 0,30" fill="var(--charcoal)"/>
    <polygon points="292,0 510,0 510,30 280,30" fill="url(#band-front)"/>
  </svg>
</section>

<section class="card card--back" aria-label="Business card back">
  <div class="brand"><span class="brand-square"></span><span class="brand-name">Northfield Homes</span></div>

  <svg class="card-bands" viewBox="0 0 510 30" aria-hidden="true">
    <defs>
      <linearGradient id="band-back" x1="0" x2="1" y1="0" y2="0">
        <stop offset="0" stop-color="var(--lime)"/>
        <stop offset="1" stop-color="var(--green-dark)"/>
      </linearGradient>
    </defs>
    <polygon points="0,14 284,14 277,30 0,30" fill="var(--charcoal)"/>
    <polygon points="292,0 510,0 510,30 280,30" fill="url(#band-back)"/>
  </svg>
</section>

</body>
</html>
```